I need an Deskworth selling website

My Deskworth store is driven by creativity and innovation. With this i am searching for an industry standard website for my Deskworth and items selling website. I sell a wide range of Deskworth items such as chairs, tables, burglary, cotton, wardrobe, etc. There will be a category for each of the items i sell. My business is based in the United States and services only US based residents. I don't accept online payments and customers are to pay on delivery of items. The website is to have images of the items i sell. I would like brown, black and golden colors because those are the colors furniture mostly make use of. Designs submitted should be unique.

Industry/Entity Type

Furniture Store

Coding

Coded - Design and coding required

```html
<!DOCTYPE html>
<html lang="en">
<head>
<meta charset="utf-8">
<title>Deskworth</title>
<link rel="stylesheet" href="https://fonts.googleapis.com/css2?family=Lato:wght@400;700&family=Questrial&display=swap">
<style>
:root{
  --gold:#efb31b;
  --ink:#111;
  --text:#666;
  --band:#f2f2f2;
  --line:#e6e6e6;
  --white:#fff;
}
*{box-sizing:border-box;margin:0;padding:0}
html,body{width:1200px;height:2281px;overflow:hidden;background:var(--white)}
body{position:relative;font-family:'Lato',sans-serif;color:var(--text)}
.abs{position:absolute}
.site-header{left:0;top:0;width:1200px;height:94px;border-bottom:1px solid #eee}
.brand{left:78px;top:22px;font-family:'Questrial',sans-serif;font-weight:400;font-size:46px;letter-spacing:4px;color:var(--ink);line-height:1}
.main-nav a{position:absolute;top:34px;font-size:15px;color:var(--gold);text-decoration:none;letter-spacing:.3px}
.heading{font-family:'Questrial',sans-serif;color:var(--ink);font-weight:400}
.hero-title{left:78px;top:262px;font-size:50px;letter-spacing:.2px}
.hero-text{left:79px;top:336px;width:500px;font-size:16.5px;line-height:24.5px;color:var(--text)}
.btn-more{left:78px;top:446px;width:187px;height:51px;background:var(--gold);border-radius:4px;color:var(--white);font-weight:700;font-size:14.5px;display:flex;align-items:center}
.btn-more .label{width:135px;text-align:center}
.btn-more .arrow{width:52px;height:100%;border-left:1px solid rgba(255,255,255,.45);display:flex;align-items:center;justify-content:center}
.hero-photo{left:654px;top:103px;width:418px;height:566px;border-radius:8px;background:linear-gradient(160deg,#e5e5e8 0%,#8a8d96 45%,#c94030 70%,#3a3a3e 100%)}
.about{left:0;top:677px;width:1200px;height:249px;background:var(--band)}
.section-title{width:1200px;left:0;text-align:center;font-size:43px}
.about-text{left:137px;top:773px;width:928px;text-align:center;font-family:Arial,sans-serif;font-size:14.8px;line-height:22.8px;color:#555}
.product-img{width:251px;height:250px;top:1052px}
.product-name{width:251px;text-align:center;font-family:'Questrial',sans-serif;font-size:20px;color:#222;line-height:24px}
.product-price{width:251px;text-align:center;font-weight:700;font-size:23px;color:var(--ink)}
.product-card{left:78px;top:1052px;width:251px;height:366px;border:1px solid #e3e3e3;box-shadow:0 0 6px rgba(0,0,0,.15);background:var(--white)}
.card-actions{left:78px;top:1375px;width:251px;height:42px;display:flex}
.add-cart{width:167px;background:var(--gold);color:var(--white);font-size:19px;display:flex;align-items:center;justify-content:center}
.card-icon{width:42px;border-left:1px solid #e3e3e3;border-top:1px solid #e3e3e3;display:flex;align-items:center;justify-content:center}
.rule{left:78px;width:1045px;height:1px;background:var(--line)}
.news-img{top:1573px;width:333px;height:187px}
.news-title{top:1774px;font-family:'Questrial',sans-serif;font-weight:400;font-size:21px;color:#222}
.news-text{top:1809px;width:330px;font-family:Arial,sans-serif;font-size:14.5px;line-height:23px;color:#555}
.news-btn{top:1875px;width:116px;height:40px;background:var(--gold);border-radius:3px;color:var(--white);font-family:Arial,sans-serif;font-size:15px;display:flex;align-items:center;justify-content:center}
.footer-col{top:1998px}
.footer-col h4{font-family:'Questrial',sans-serif;font-weight:400;font-size:21px;color:var(--ink);margin-bottom:10px;letter-spacing:.3px}
.footer-col li{list-style:none;font-size:14.5px;line-height:25px;color:#666}
.footer-col li::before{content:"» ";color:#888;margin-right:4px}
.footer-col li.current{font-weight:700;color:#333}
.bottom-bar{left:0;top:2218px;width:1200px;height:63px;background:var(--gold)}
.copyright{left:79px;top:2240px;font-size:13.5px;color:var(--white);font-family:Arial,sans-serif;font-weight:700}
.copyright b{color:var(--ink)}
</style>
</head>
<body>

<header class="abs site-header">
  <div class="abs brand">DESKWORTH</div>
  <nav class="main-nav">
    <a style="left:566px">HOME</a>
    <a style="left:648px">ABOUT</a>
    <a style="left:735px">PRODUCTS</a>
    <a style="left:852px">CASE STUDY</a>
    <a style="left:978px">NEWS</a>
    <a style="left:1048px">CONTACT</a>
  </nav>
</header>

<section class="hero">
  <h1 class="abs heading hero-title">Task &amp; Meeting Chairs</h1>
  <p class="abs hero-text">Lorem Ipsum is simply dummy text of the printing and typesetting industry. Lorem Ipsum has been the industry's standard dummy text ever since the 1500s</p>
  <div class="abs btn-more"><span class="label">VIEW MORE</span><span class="arrow">
    <svg width="14" height="12" viewBox="0 0 14 12"><path d="M1 1l5 5-5 5M7 1l5 5-5 5" fill="none" stroke="#fff" stroke-width="2"/></svg></span></div>
  <div class="abs hero-photo" role="img" aria-label="Man seated on a red task chair"></div>
</section>

<section class="abs about"></section>
<h2 class="abs heading section-title" style="top:712px">About...</h2>
<p class="abs about-text">Lorem Ipsum is simply dummy text of the printing and typesetting industry. Lorem Ipsum has been the industry's standard dummy text ever since the 1500s, when an unknown printer took a galley of type and scrambled it to make a type specimen book. It has survived not only five centuries, but also the leap into electronic typesetting, remaining essentially unchanged. It was popularised in the 1960s with the release of Lettersheet sheets containing Lorem Ipsum passages, and more recently with desktop publishing software like Folio Layout including versions of Lorem Ipsum.</p>

<h2 class="abs heading section-title" style="top:970px">Products...</h2>

<div class="abs product-card"></div>
<div class="abs product-img" style="left:79px;top:1053px;width:249px;height:230px;background:radial-gradient(circle at 50% 50%,#d02020 0%,#b01818 35%,#f4f4f4 60%)" role="img" aria-label="Red lounge pod chair with white cushion"></div>
<div class="abs product-name" style="left:78px;top:1290px">Lorem ipsum is</div>
<div class="abs product-price" style="left:78px;top:1330px">$200.00</div>
<div class="abs card-actions">
  <div class="add-cart">Add To Cart</div>
  <div class="card-icon"><svg width="16" height="14" viewBox="0 0 16 14"><path d="M8 13L2 7a3.5 3.5 0 0 1 6-4 3.5 3.5 0 0 1 6 4z" fill="#888"/></svg></div>
  <div class="card-icon"><svg width="16" height="10" viewBox="0 0 16 10"><ellipse cx="8" cy="5" rx="7" ry="4.2" fill="none" stroke="#888" stroke-width="1.4"/><circle cx="8" cy="5" r="2" fill="#888"/></svg></div>
</div>

<div class="abs product-img" style="left:343px;background:radial-gradient(circle at 50% 45%,#e6c89a 0%,#efe6da 40%,#f2f2f2 70%)" role="img" aria-label="Round wooden side table"></div>
<div class="abs product-name" style="left:343px;top:1322px">Lorem ipsum is</div>
<div class="abs product-price" style="left:343px;top:1381px">$50.00</div>

<div class="abs product-img" style="left:607px;background:radial-gradient(circle at 50% 50%,#b8b9bd 0%,#d9d1a0 35%,#f2f2f2 70%)" role="img" aria-label="Metal filing cabinet with binders"></div>
<div class="abs product-name" style="left:607px;top:1322px">Lorem Ipsum is simply<br>dummy text</div>
<div class="abs product-price" style="left:607px;top:1381px">$399.00</div>

<div class="abs product-img" style="left:872px;background:radial-gradient(circle at 50% 50%,#2a2a3a 0%,#6b6e85 30%,#f2f2f2 65%)" role="img" aria-label="Black corner computer desk"></div>
<div class="abs product-name" style="left:872px;top:1322px">Lorem Ipsum is simply</div>
<div class="abs product-price" style="left:872px;top:1381px">$296.00</div>

<div class="abs rule" style="top:1469px"></div>

<h2 class="abs heading section-title" style="top:1501px">News...</h2>

<div class="abs news-img" style="left:78px;background:linear-gradient(180deg,#dfe6ea 0%,#7c8ed8 50%,#9a9692 100%)" role="img" aria-label="Blue lounge seating in a lobby, video"></div>
<svg class="abs" style="left:217px;top:1640px" width="54" height="54" viewBox="0 0 54 54"><circle cx="27" cy="27" r="27" fill="rgba(40,40,40,.75)"/><path d="M21 16l18 11-18 11z" fill="#fff"/></svg>
<div class="abs news-img" style="left:434px;background:linear-gradient(180deg,#c9a25a 0%,#d66c1c 55%,#3e3a36 100%)" role="img" aria-label="Office lounge with orange armchairs"></div>
<div class="abs news-img" style="left:789px;background:linear-gradient(180deg,#eef0ee 0%,#b9c2b2 50%,#8f8a7c 100%)" role="img" aria-label="Bright open office with plants and copier"></div>

<h3 class="abs news-title" style="left:79px">Lorem Ipsum is simply dummy</h3>
<h3 class="abs news-title" style="left:435px">Lorem Ipsum is simply dummy</h3>
<h3 class="abs news-title" style="left:792px">Lorem Ipsum is simply dummy</h3>
<p class="abs news-text" style="left:79px">Lorem Ipsum is simply dummy text of the printing and typesetting industry.</p>
<p class="abs news-text" style="left:435px">Lorem Ipsum is simply dummy text of the printing and typesetting industry.</p>
<p class="abs news-text" style="left:792px">Lorem Ipsum is simply dummy text of the printing and typesetting industry.</p>
<div class="abs news-btn" style="left:78px">VIEW MORE</div>
<div class="abs news-btn" style="left:434px">VIEW MORE</div>
<div class="abs news-btn" style="left:789px">VIEW MORE</div>

<div class="abs rule" style="top:1970px"></div>

<footer>
  <div class="abs footer-col" style="left:79px"><h4>LINKS</h4><ul>
    <li class="current">Home</li><li>About</li><li>Products</li><li>Case Study</li><li>News</li><li>Contact</li></ul></div>
  <div class="abs footer-col" style="left:345px"><h4>PRODUCTS</h4><ul>
    <li>Chair</li><li>Table</li><li>Burglary Safe Cupboard</li><li>Wordrobe</li><li>Workspace Storage</li><li>Bins &amp; Bags</li></ul></div>
  <div class="abs footer-col" style="left:608px"><h4>ACCOUNT</h4><ul>
    <li>My Account</li><li>Order History</li><li>Wish List</li><li>Newsletter</li><li>Specials</li></ul></div>
  <div class="abs footer-col" style="left:873px"><h4>CUSTOMER SERVICE</h4><ul>
    <li>Contact Us</li><li>Privacy Policy</li><li>Terms Of Use</li><li>Return Policy</li><li>Site Map</li><li>Gift Vouchers</li></ul></div>

  <div class="abs bottom-bar"></div>
  <div class="abs copyright">© <b>DESKWORTH</b> - 2016. All Rights Reserved.</div>
  <svg class="abs" style="left:938px;top:2226px" width="186" height="46" viewBox="0 0 186 46">
    <circle cx="23" cy="23" r="21" fill="#fff"/>
    <circle cx="68" cy="23" r="20" fill="none" stroke="rgba(255,255,255,.7)" stroke-width="1.5"/>
    <circle cx="116" cy="23" r="20" fill="none" stroke="rgba(255,255,255,.7)" stroke-width="1.5"/>
    <circle cx="163" cy="23" r="20" fill="none" stroke="rgba(255,255,255,.7)" stroke-width="1.5"/>
  </svg>
</footer>

</body>
</html>
```